Business Card Design

We need a business card designed for a new company based in Melbourne called Kvt solutions. Kvt solutions provides management consulting specialising in the health and social services sector.

Kvt solutions offer a unique set of specialist skills │dealing with all levels of government │ unique communication skills│intimate knowledge of the health sector │solutions tailored to unique circumstances.

Kvt solutions takes on a select number of clients at any one time, this ensures that your organisation receives the attention required. On larger projects, Kvt solutions join up with other consultants to bring specialist skills to a project.
Updates

This is the first time I have used Pixel Harbor and thank you all for responding. The variation is amazing and makes it hard to decide. I have to ask some of my friends to give me their views. The response is fantastic. The one I pick will basically be the most visually appealing

Industry/Entity Type

Management Consulting

Contact Information for Business Card

Martin Oakes, Principal, Kvt solutions, 14 Wexcombe Ave, Larkdale VIC 3189, 0417 382 914, martino@kvtsolutions-example.com.au, www.kvtsolutions-example.com.au

```html
<!DOCTYPE html>
<html lang="en">
<head>
<meta charset="utf-8">
<title>Kvt solutions – Business Card</title>
<link rel="stylesheet" href="https://fonts.googleapis.com/css2?family=Roboto+Slab:wght@400&family=PT+Sans:wght@400&display=swap">
<style>
  :root {
    --backdrop: #d9d6d1;
    --card-white: #ffffff;
    --grid-tint: #eeeeee;
    --ink: #231f20;
    --brand-red: #e31b23;
    --deep-red: #b5121b;
    --text-light: #ffffff;
  }
  html, body {
    margin: 0;
    width: 1200px;
    height: 914px;
    overflow: hidden;
    background: var(--backdrop);
  }
  .card {
    position: absolute;
    left: 100px;
    top: 151px;
    width: 1000px;
    height: 611px;
    box-shadow: 0 10px 30px rgba(0,0,0,0.25);
  }
  .card svg { display: block; width: 100%; height: 100%; }
  .name, .brand-name, .tagline {
    font-family: "Roboto Slab", serif;
    fill: var(--deep-red);
  }
  .name { font-size: 34px; letter-spacing: 1px; }
  .brand-name { font-size: 62px; }
  .tagline { font-size: 16px; letter-spacing: 1px; }
  .contact {
    font-family: "PT Sans", sans-serif;
    font-size: 29px;
    fill: var(--text-light);
  }
  .icon-disc { fill: var(--brand-red); }
  .icon-glyph { fill: var(--text-light); }
  .icon-line { fill: none; stroke: var(--text-light); stroke-width: 2.5; }
</style>
</head>
<body>
  <div class="card">
    <svg viewBox="0 0 1000 611" xmlns="http://www.w3.org/2000/svg">
      <defs>
        <linearGradient id="grid-wash" x1="0" y1="0" x2="1" y2="1">
          <stop offset="0" stop-color="#f4f4f4"/>
          <stop offset="1" stop-color="#e9e9e9"/>
        </linearGradient>
      </defs>

      <!-- light patterned upper field -->
      <rect class="upper-field" x="0" y="0" width="1000" height="611" fill="url(#grid-wash)"
            role="img" aria-label="Light grey grid pattern of small plus marks"/>

      <!-- thin dark accent line -->
      <path class="accent-line" d="M0,160 C260,120 450,170 590,320 C720,460 860,500 1000,470"
            fill="none" stroke="var(--ink)" stroke-width="3"/>

      <!-- red swoosh band -->
      <path class="swoosh" d="M60,172 C300,135 480,205 615,345 C740,470 870,500 1000,485
                              L1000,565 C820,560 690,505 570,380 C450,255 300,185 60,172 Z"
            fill="var(--brand-red)"/>

      <!-- dark lower field -->
      <path class="lower-field" d="M0,178 C270,165 440,230 560,370 C680,505 830,575 1000,570
                                   L1000,611 L0,611 Z" fill="var(--ink)"/>

      <!-- identity -->
      <text class="name" x="570" y="118">Martin Oakes</text>
      <text class="brand-name" x="520" y="205">Kvt solutions</text>
      <text class="tagline" x="548" y="245">HEALTH &amp; SOCIAL SERVICES CONSULTING</text>

      <!-- address -->
      <g class="contact-row">
        <circle class="icon-disc" cx="55" cy="288" r="19"/>
        <path class="icon-glyph" d="M55,276 a8,8 0 0 1 8,8 c0,6 -8,15 -8,15 c0,0 -8,-9 -8,-15 a8,8 0 0 1 8,-8 Z"/>
        <circle cx="55" cy="284" r="3" fill="var(--brand-red)"/>
        <text class="contact" x="112" y="298">Kvt solutions, 14 Wexcombe Ave,</text>
        <text class="contact" x="112" y="338">Larkdale VIC 3189.</text>
      </g>

      <!-- phone -->
      <g class="contact-row">
        <circle class="icon-disc" cx="55" cy="380" r="19"/>
        <rect class="icon-line" x="48" y="368" width="14" height="24" rx="2"/>
        <text class="contact" x="112" y="390">0417 382 914</text>
      </g>

      <!-- email -->
      <g class="contact-row">
        <circle class="icon-disc" cx="55" cy="440" r="19"/>
        <rect class="icon-glyph" x="43" y="432" width="24" height="16" rx="1"/>
        <path d="M43,433 L55,442 L67,433" fill="none" stroke="var(--brand-red)" stroke-width="2"/>
        <text class="contact" x="112" y="450">martino@kvtsolutions-example.com.au</text>
      </g>

      <!-- web -->
      <g class="contact-row">
        <circle class="icon-disc" cx="55" cy="502" r="19"/>
        <circle class="icon-line" cx="55" cy="502" r="10"/>
        <ellipse class="icon-line" cx="55" cy="502" rx="4" ry="10"/>
        <path class="icon-line" d="M45,502 H65"/>
        <text class="contact" x="112" y="512">www.kvtsolutions-example.com.au</text>
      </g>
    </svg>
  </div>
</body>
</html>
```